Bookcover: Ways to Turn Into a Bold Pathfinder

I am publishing a super-low-cost innovation book for €4,99 on Quillmere Open Press to help everyone become a great innovator: young ambitious people without college education nor a big budget. Do you want to help me?

Brief:
Design a book cover 1600 x 2560 pixels for QOP.
Main title: Ways to Turn Into a Bold Pathfinder
Sub title: mindset - insights - skills & tools
Author: Joost ter Brakel
Design: captive, and appealing to everyone
Target Group: young ambitious people without college education

For quillmere please format the height/width ratio of 1.6:1

```html
<!DOCTYPE html>
<html lang="en">
<head>
<meta charset="UTF-8">
<title>Ways to Turn Into a Bold Pathfinder — Book Cover</title>
<link href="https://fonts.googleapis.com/css2?family=Lato:wght@400;900&family=Rubik:wght@500&family=Roboto:ital,wght@1,400&display=swap" rel="stylesheet">
<style>
  :root {
    --page-bg: #ffffff;
    --cover-edge: #fbdd5f;
    --cover-mid: #fdef86;
    --cover-glow: #fffc9c;
    --ink: #111111;
    --art-white: #ffffff;
    --art-teal: #5fcfd0;
    --art-pink: #e8386d;
    --art-bulb: #f8d54a;
  }
  * { margin: 0; padding: 0; box-sizing: border-box; }
  html, body {
    width: 1200px;
    height: 1200px;
    overflow: hidden;
    background: var(--page-bg);
  }
  .canvas {
    position: relative;
    width: 1200px;
    height: 1200px;
  }
  .book-cover {
    position: absolute;
    left: 250px;
    top: 40px;
    width: 700px;
    height: 1120px;
    background: radial-gradient(ellipse 70% 55% at 50% 55%, var(--cover-glow) 0%, var(--cover-mid) 55%, var(--cover-edge) 100%);
    color: var(--ink);
    text-align: center;
    overflow: hidden;
  }
  .book-title { font-weight: normal; }
  .title-lead,
  .title-main {
    position: absolute;
    left: 0;
    right: 0;
    display: block;
    font-family: "Lato", sans-serif;
    line-height: 1;
    text-transform: uppercase;
  }
  .title-lead {
    top: 88px;
    font-weight: 400;
    font-size: 50px;
    letter-spacing: -1px;
  }
  .title-main { font-weight: 900; }
  .title-main--first {
    top: 152px;
    font-size: 120px;
    letter-spacing: 10px;
  }
  .title-main--second {
    top: 266px;
    font-size: 98px;
    letter-spacing: -1px;
  }
  .subtitle {
    position: absolute;
    top: 374px;
    left: 0;
    right: 0;
    font-family: "Rubik", sans-serif;
    font-weight: 500;
    font-size: 33px;
    line-height: 1;
  }
  .cover-art {
    position: absolute;
    left: 20px;
    top: 428px;
    width: 660px;
    height: 580px;
  }
  .author {
    position: absolute;
    top: 1030px;
    left: 0;
    right: 0;
    font-family: "Roboto", sans-serif;
    font-style: italic;
    font-weight: 400;
    font-size: 44px;
    line-height: 1;
  }
</style>
</head>
<body>
  <main class="canvas">
    <section class="book-cover">
      <h1 class="book-title">
        <span class="title-lead">Ways to Turn Into</span>
        <span class="title-main title-main--first">A Bold</span>
        <span class="title-main title-main--second">Pathfinder</span>
      </h1>
      <p class="subtitle">Mindset - Insights - Skills &amp; Tools</p>
      <svg class="cover-art" viewBox="0 0 660 580" role="img" aria-label="Illustration: profile of a head with a glowing light bulb inside, surrounded by doodled gears, coins, charts, speech bubbles, arrows and a megaphone">
        <defs>
          <radialGradient id="artFill" cx="55%" cy="48%" r="62%">
            <stop offset="0%" stop-color="var(--art-white)"/>
            <stop offset="38%" stop-color="var(--art-white)"/>
            <stop offset="62%" stop-color="var(--art-bulb)" stop-opacity="0.55"/>
            <stop offset="82%" stop-color="var(--art-teal)" stop-opacity="0.45"/>
            <stop offset="100%" stop-color="var(--art-pink)" stop-opacity="0.4"/>
          </radialGradient>
        </defs>
        <rect class="cover-art__area" x="0" y="0" width="660" height="580" rx="40" fill="url(#artFill)"/>
      </svg>
      <p class="author">Joost ter Brakel</p>
    </section>
  </main>
</body>
</html>
```